Business Card Design

We need a business card designed for our new company. Prefer a black card with white logo & writing.

Contact Information for Business Card

Ted Galloway, address: 7-4812 Fernhollow Road, Abbotsford, BC, V3K 8R2, Office Phone: 604-712-3390, Cell: 604-947-2164, Email: ted@resinworkshub.ca

Colors

Designer to choose only greyscale colors for use in the design.

```html
<!DOCTYPE html>
<html lang="en">
<head>
<meta charset="utf-8">
<title>Resin Works Hub — Business Card</title>
<link rel="stylesheet" href="https://fonts.googleapis.com/css2?family=Montserrat:wght@400;500;700&display=swap">
<style>
  :root {
    --backdrop: #d9d9d9;
    --card: #262626;
    --ink: #ffffff;
    --ink-soft: #e6e6e6;
    --shadow: rgba(0, 0, 0, 0.35);
  }
  * { margin: 0; padding: 0; box-sizing: border-box; }
  html, body { width: 900px; height: 1200px; overflow: hidden; }
  body {
    background: var(--backdrop);
    font-family: "Montserrat", sans-serif;
    color: var(--ink);
    position: relative;
  }
  .card {
    position: absolute;
    left: 80px;
    width: 742px;
    height: 442px;
    background: var(--card);
    border-radius: 24px;
    box-shadow: 0 6px 18px var(--shadow);
  }
  .card--front { top: 130px; }
  .card--back { top: 638px; }

  .brand {
    position: absolute;
    text-align: center;
    font-weight: 700;
    color: var(--ink);
    text-transform: uppercase;
    line-height: 1.1;
  }
  .brand__mark {
    display: block;
    margin: 0 auto;
    background: var(--ink);
  }
  .card--front .brand {
    left: 160px; top: 178px; width: 200px;
    font-size: 22px; letter-spacing: 1px;
  }
  .card--front .brand__mark { width: 12px; height: 12px; margin-bottom: 10px; }
  .card--back .brand {
    left: 171px; top: 130px; width: 400px;
    font-size: 54px; letter-spacing: 2px;
  }
  .card--back .brand__mark { width: 26px; height: 26px; margin-bottom: 18px; }

  .divider {
    position: absolute;
    left: 371px; top: 135px;
    width: 3px; height: 177px;
    background: var(--ink);
  }
  .person { position: absolute; left: 392px; top: 128px; }
  .person__name { font-size: 24px; font-weight: 700; line-height: 1.2; }
  .person__role { font-size: 15px; font-weight: 400; color: var(--ink-soft); margin-top: 4px; }

  .contacts { position: absolute; left: 393px; top: 209px; list-style: none; }
  .contacts li {
    display: flex; align-items: center;
    font-size: 15.5px; font-weight: 400;
    height: 26.5px;
  }
  .contacts li:nth-child(2) { margin-top: 3px; }
  .contacts svg { width: 17px; height: 17px; margin-right: 11px; flex: none; }

  .address {
    position: absolute;
    left: 0; right: 0; top: 376px;
    text-align: center;
    font-size: 15.5px; font-weight: 400;
  }
</style>
</head>
<body>
  <section class="card card--front">
    <div class="brand">
      <span class="brand__mark"></span>
      Resin Works<br>Hub
    </div>
    <div class="divider"></div>
    <div class="person">
      <h1 class="person__name">Ted Galloway</h1>
      <p class="person__role">owner</p>
    </div>
    <ul class="contacts">
      <li>
        <svg viewBox="0 0 24 24" fill="none" stroke="#fff" stroke-width="2" stroke-linecap="round" stroke-linejoin="round" aria-hidden="true"><path d="M5 3h4l2 5-3 2a12 12 0 0 0 6 6l2-3 5 2v4a2 2 0 0 1-2 2A17 17 0 0 1 3 5a2 2 0 0 1 2-2z"/><path d="M15 3a6 6 0 0 1 6 6M15 7a2 2 0 0 1 2 2"/></svg>
        604-712-3390
      </li>
      <li>
        <svg viewBox="0 0 24 24" fill="none" stroke="#fff" stroke-width="2" stroke-linecap="round" aria-hidden="true"><rect x="6" y="2" width="12" height="20" rx="2"/><path d="M11 18h2"/></svg>
        604-947-2164
      </li>
      <li>
        <svg viewBox="0 0 24 24" aria-hidden="true"><rect x="3" y="6" width="18" height="12" rx="1" fill="#fff"/><path d="M3 7l9 6 9-6" fill="none" stroke="#262626" stroke-width="1.6"/></svg>
        ted@resinworkshub.ca
      </li>
      <li>
        <svg viewBox="0 0 24 24" fill="none" stroke="#fff" stroke-width="2" aria-hidden="true"><circle cx="12" cy="12" r="9"/><path d="M3 12h18M12 3c3 3 3 15 0 18M12 3c-3 3-3 15 0 18"/></svg>
        www.resinworkshub.ca
      </li>
    </ul>
    <p class="address">7-4812 Fernhollow Road, Abbotsford, BC, V3K 8R2</p>
  </section>

  <section class="card card--back">
    <div class="brand">
      <span class="brand__mark"></span>
      Resin Works<br>Hub
    </div>
  </section>
</body>
</html>
```